R7M Horizon Business Card Design

We need a business card created for our New Business "R7M Horizon"<br/><br/>The business card design is up to you however the following information must be on the business card:<br/><br/>Front of the business card -<br/>Email :darrenp@r7mhorizon.nz<br/>Mobile: +64 (0) 22 4870 619<br/>Website: www.r7mhorizon.nz<br/>Card Owner Name: Darren Paltrow<br/>Company Title: Business Development Manager<br/>Slogan: "The BEST of both worlds". <br/>Logo On the front attached to the design brief<br/><br/>On the back: <br/>Space on the back for 4 more versions of the logo across the bottom of the card indicating different subsidiary brands - R7M Coffee, R7M Arts, R7M ?? (The card will be used for all of these brands - We Will add the extra subsidiary logos to the design once the design is finished (We are a graphics design team). <br/><br/>Other than that we want a premium feeling logo that remains universally usable depending on the business entity that we are using the card for. The use of bright bold colours would be great but we still want the card to feel premium.
Target Market(s)
Gift Design and Manufacturing Companies
Contact Information for Business Card
Front of the business card -
Email :darrenp@r7mhorizon.nz
Mobile: +64 (0) 22 4870 619
Website: www.r7mhorizon.nz
Card Owner Name: Darren Paltrow
Company Title: Business Development Manager
Slogan: "The BEST of both worlds".
Logo On the front attached to the design brief

```html
<!DOCTYPE html>
<html lang="en">
<head>
<meta charset="UTF-8">
<title>R7M Horizon Business Card</title>
<link href="https://fonts.googleapis.com/css2?family=Open+Sans:ital,wght@0,400;0,600;0,700;1,700&display=swap" rel="stylesheet">
<style>
  :root {
    --backdrop: #2b2b2d;
    --card: #1c1c1d;
    --brand-blue: #3d4fb0;
    --text-light: #f2f2f2;
    --text-soft: #d9d9d9;
  }
  * { box-sizing: border-box; margin: 0; padding: 0; }
  html, body {
    width: 1200px; height: 900px; overflow: hidden;
    background: var(--backdrop);
    font-family: "Open Sans", Arial, sans-serif;
  }
  .stage {
    width: 1200px; height: 900px;
    display: flex; flex-direction: column; align-items: center; justify-content: center;
    gap: 50px;
  }
  .card {
    width: 620px; height: 354px;
    background: var(--card);
    position: relative;
    box-shadow: 0 14px 30px rgba(0,0,0,0.45);
  }
  .brand {
    display: flex; align-items: center; gap: 12px;
    color: var(--brand-blue); font-weight: 700; white-space: nowrap;
  }
  .brand-ring {
    border: 6px solid var(--brand-blue); border-radius: 50%; flex: none;
  }
  /* Front */
  .card-front .brand {
    position: absolute; left: 40px; top: 120px; font-size: 30px;
  }
  .card-front .brand-ring { width: 44px; height: 44px; }
  .divider {
    position: absolute; left: 318px; top: 96px;
    width: 2px; height: 130px; background: var(--brand-blue);
  }
  .details { position: absolute; left: 340px; top: 100px; }
  .holder-name {
    color: var(--brand-blue); font-weight: 700; font-size: 21px;
    text-transform: uppercase; letter-spacing: 0.5px;
  }
  .holder-title { color: var(--text-light); font-size: 14px; margin-top: 2px; }
  .contact-list { list-style: none; margin-top: 16px; }
  .contact-list li {
    display: flex; align-items: center; gap: 8px;
    color: var(--text-light); font-size: 14px; line-height: 22px;
  }
  .contact-list svg { width: 12px; height: 12px; flex: none; }
  .slogan {
    position: absolute; left: 70px; top: 262px;
    color: var(--text-soft); font-size: 15px;
  }
  .slogan strong { color: var(--text-light); font-weight: 700; }
  /* Back */
  .card-back .brand {
    position: absolute; left: 50%; top: 50%; transform: translate(-50%, -50%);
    font-size: 48px; gap: 18px;
  }
  .card-back .brand-ring { width: 70px; height: 70px; border-width: 9px; }
</style>
</head>
<body>
<main class="stage">
  <section class="card card-front" aria-label="Business card front">
    <div class="brand"><span class="brand-ring"></span>R7M Horizon</div>
    <div class="divider"></div>
    <div class="details">
      <p class="holder-name">Darren Paltrow</p>
      <p class="holder-title">Business Development Manager</p>
      <ul class="contact-list">
        <li>
          <svg viewBox="0 0 12 12" aria-hidden="true"><rect x="3" y="0.5" width="6" height="11" rx="1" fill="none" stroke="#3d4fb0" stroke-width="1.2"/><rect x="5" y="9" width="2" height="1" fill="#3d4fb0"/></svg>
          +64 (0) 22 4870 619
        </li>
        <li>
          <svg viewBox="0 0 12 12" aria-hidden="true"><rect x="0.5" y="2.5" width="11" height="7.5" fill="#3d4fb0"/><path d="M0.5 2.5 L6 7 L11.5 2.5" fill="none" stroke="#1c1c1d" stroke-width="1"/></svg>
          darrenp@r7mhorizon.nz
        </li>
        <li>
          <svg viewBox="0 0 12 12" aria-hidden="true"><circle cx="6" cy="6" r="5.3" fill="none" stroke="#3d4fb0" stroke-width="1.2"/><ellipse cx="6" cy="6" rx="2.2" ry="5.3" fill="none" stroke="#3d4fb0" stroke-width="1"/><line x1="0.7" y1="6" x2="11.3" y2="6" stroke="#3d4fb0" stroke-width="1"/></svg>
          www.r7mhorizon.nz
        </li>
      </ul>
    </div>
    <p class="slogan">The <strong>BEST</strong> of both worlds</p>
  </section>

  <section class="card card-back" aria-label="Business card back">
    <div class="brand"><span class="brand-ring"></span>R7M Horizon</div>
  </section>
</main>
</body>
</html>
```